Boutique custom software development company needs new business card

Our nearly 20 year old custom software development company would like to better include the fact that we are now providing Bitcoin services. These new services are B2B include education (how to acquire and securely hold Bitcoin) and integrating Bitcoin payments into existing ecommerce sites or other existing systems. Please keep the card clean and simple. Attached is our current design and some other files. vextorial.com

Target Market(s)

businesses owners interested in long term relationship

Industry/Entity Type

Custom software development and Bitcoin

Contact Information for Business Card

Dale Parker, dale@vextorial.com, vextorial.com, (888) 555-VXTRL

Font styles to use
Other font styles liked:
• monospace

Requirements
Must have
• double-sided
Nice to have
• clean and simple
Should not have
• physical address

```html
<!DOCTYPE html>
<html lang="en">
<head>
<meta charset="utf-8">
<title>Vextorial business card</title>
<link rel="stylesheet" href="https://fonts.googleapis.com/css2?family=Montserrat:wght@400;500;600&display=swap">
<style>
  :root {
    --backdrop: #161616;
    --card: #262626;
    --orange: #f47b20;
    --blue: #3b74c4;
    --ink: #ffffff;
  }
  * { margin: 0; padding: 0; box-sizing: border-box; }
  html, body { width: 1200px; height: 900px; overflow: hidden; }
  body {
    background: var(--backdrop);
    font-family: "Montserrat", sans-serif;
    display: flex;
    flex-direction: column;
    align-items: center;
    justify-content: center;
    gap: 48px;
  }
  .card {
    position: relative;
    width: 630px;
    height: 360px;
    background: var(--card);
    border-radius: 18px;
    overflow: hidden;
    box-shadow: 0 10px 30px rgba(0,0,0,.5);
  }

  /* front */
  .front .accent-tick {
    position: absolute; left: 0; top: 44px;
    width: 10px; height: 30px; background: var(--orange);
  }
  .front .identity { position: absolute; left: 40px; top: 40px; }
  .front .name {
    font-size: 26px; font-weight: 500; letter-spacing: 1px;
    text-transform: uppercase; line-height: 1;
  }
  .front .name .first { color: var(--orange); }
  .front .name .last { color: var(--blue); }
  .front .role {
    margin-top: 6px; font-size: 15px; color: var(--ink);
    letter-spacing: 1px; text-transform: uppercase;
  }
  .front .divider {
    position: absolute; left: 40px; right: 40px; top: 112px;
    height: 1px; background: var(--blue);
  }
  .front .contact-list {
    position: absolute; left: 40px; top: 128px;
    list-style: none; font-size: 15px; color: var(--ink);
    letter-spacing: .5px;
  }
  .front .contact-list li {
    display: flex; align-items: center; gap: 10px; line-height: 24px;
  }
  .front .contact-list svg { width: 13px; height: 13px; flex: none; }
  .front .web .hl { color: var(--blue); }
  .front .brand {
    position: absolute; right: 40px; top: 48px; text-align: right;
  }
  .brand-name {
    font-weight: 600; color: var(--blue); letter-spacing: 1px;
    display: flex; align-items: center; gap: 10px; line-height: 1;
  }
  .brand-mark { background: var(--orange); flex: none; }
  .tagline { color: var(--blue); font-weight: 400; }
  .front .brand-name { font-size: 30px; justify-content: flex-end; }
  .front .brand-mark { width: 18px; height: 18px; }
  .front .tagline { font-size: 12px; margin-top: 6px; }
  .front .services {
    position: absolute; right: 40px; bottom: 48px;
    list-style: none; text-align: right;
    font-size: 15px; line-height: 22px; color: var(--ink); letter-spacing: .5px;
  }
  .front .services .hl { color: var(--orange); }
  .front .edge-band {
    position: absolute; left: 0; right: 0; bottom: 0; height: 8px;
    background: linear-gradient(90deg, var(--orange) 0 48%, var(--blue) 48% 100%);
  }

  /* back */
  .back {
    display: flex; flex-direction: column;
    align-items: center; justify-content: center;
  }
  .back .brand-name { font-size: 60px; }
  .back .brand-mark { width: 36px; height: 36px; }
  .back .tagline { font-size: 21px; margin-top: 10px; }
</style>
</head>
<body>

  <section class="card front" aria-label="Card front">
    <span class="accent-tick"></span>
    <div class="identity">
      <h1 class="name"><span class="first">Dale</span> <span class="last">Parker</span></h1>
      <p class="role">Director</p>
    </div>
    <span class="divider"></span>
    <ul class="contact-list">
      <li>
        <svg viewBox="0 0 16 16" aria-hidden="true"><path d="M4 1l3 3-2 2c1 2 3 4 5 5l2-2 3 3-2 2C8 14 2 8 2 3z" fill="none" stroke="#3b74c4" stroke-width="1.4"/></svg>
        (888) 555-VXTRL
      </li>
      <li>
        <svg viewBox="0 0 16 16" aria-hidden="true"><rect x="1.5" y="3.5" width="13" height="9" fill="none" stroke="#3b74c4" stroke-width="1.4"/><path d="M1.5 3.5L8 9l6.5-5.5" fill="none" stroke="#3b74c4" stroke-width="1.4"/></svg>
        dale@vextorial.com
      </li>
      <li class="web">
        <svg viewBox="0 0 16 16" aria-hidden="true"><circle cx="8" cy="8" r="6.5" fill="none" stroke="#3b74c4" stroke-width="1.3"/><ellipse cx="8" cy="8" rx="3" ry="6.5" fill="none" stroke="#3b74c4" stroke-width="1.1"/><path d="M1.5 8h13" stroke="#3b74c4" stroke-width="1.1"/></svg>
        <span>www.<span class="hl">vextorial</span>.com</span>
      </li>
    </ul>
    <div class="brand">
      <p class="brand-name"><span class="brand-mark"></span>VEXTORIAL</p>
      <p class="tagline">developer of custom applications</p>
    </div>
    <ul class="services">
      <li>Custom Software Development</li>
      <li><span class="hl">Bitcoin</span> Education &amp; Custody</li>
      <li><span class="hl">Bitcoin</span> Payment Integration</li>
    </ul>
    <span class="edge-band"></span>
  </section>

  <section class="card back" aria-label="Card back">
    <p class="brand-name"><span class="brand-mark"></span>VEXTORIAL</p>
    <p class="tagline">developer of custom applications</p>
  </section>

</body>
</html>
```